Business Card Design

We need the business card for our new business based in St. Marys, we manufacture mainly bubble wraps. And we would like the design to use our company logo and also make it easy for people to understand right away we are bubble wrap manufacturer

Industry/Entity Type

Business

Contact Information for Business Card

Cushtane Pty Ltd, 14 Larkin Road Brenmoor NSW 2764, Tel: 02 9471 5826, Fax: 9471 5839, Dara Oyelaran, General Manager, Mobile :0438 217 564, dara.oyelaran@cushtane.com.au, Website: cushtane.com.au

```html
<!DOCTYPE html>
<html lang="en">
<head>
<meta charset="utf-8">
<title>Cushtane Business Card</title>
<link rel="stylesheet" href="https://fonts.googleapis.com/css2?family=Montserrat:wght@400;500;700;800&display=swap">
<style>
  :root {
    --backdrop: #dcdcdc;
    --card-black: #0b0b0b;
    --card-black-soft: #262626;
    --brand-red: #c8262c;
    --logo-grey: #8a8886;
    --tagline-grey: #5e5c5b;
    --paper: #ffffff;
    --ink: #4a4a4a;
  }
  * { box-sizing: border-box; margin: 0; padding: 0; }
  html, body {
    width: 1200px; height: 852px; overflow: hidden;
    background: var(--backdrop);
    font-family: "Montserrat", Arial, sans-serif;
  }
  .stage {
    width: 1200px; height: 852px;
    display: flex; align-items: center; justify-content: center; gap: 40px;
  }
  .card {
    position: relative;
    width: 540px; height: 310px;
    border-radius: 14px;
    overflow: hidden;
    box-shadow: 0 6px 18px rgba(0,0,0,0.22);
  }
  /* Front */
  .card-front {
    background: linear-gradient(115deg, var(--card-black) 0%, var(--card-black-soft) 48%, var(--card-black) 60%, var(--card-black) 100%);
    display: flex; flex-direction: column; align-items: center; justify-content: center;
  }
  .brand-name {
    font-weight: 800;
    font-size: 66px;
    letter-spacing: 1px;
    color: var(--logo-grey);
    line-height: 1;
  }
  .brand-tagline {
    margin-top: 12px;
    font-weight: 500;
    font-size: 13.5px;
    letter-spacing: 5.2px;
    color: var(--tagline-grey);
  }
  /* Back */
  .card-back { background: var(--paper); }
  .card-back .wave {
    position: absolute; inset: 0; width: 100%; height: 100%;
  }
  .contact {
    position: absolute; left: 250px; right: 20px; top: 0; bottom: 0;
    color: var(--ink);
  }
  .person-name {
    position: absolute; top: 38px; left: 0;
    font-weight: 700; font-size: 17px; color: var(--brand-red); letter-spacing: 0.5px;
  }
  .person-title {
    position: absolute; top: 60px; left: 0;
    font-size: 11px; color: var(--ink);
  }
  .details {
    position: absolute; left: 0; bottom: 34px;
    list-style: none; font-size: 13px; line-height: 20px;
  }
  .details li { display: flex; align-items: center; gap: 8px; }
  .details .address { margin-bottom: 2px; }
  .details svg { width: 12px; height: 12px; flex: none; fill: var(--brand-red); }
</style>
</head>
<body>
<main class="stage">
  <section class="card card-front" aria-label="Card front">
    <div class="brand-name">CUSHTANE</div>
    <div class="brand-tagline">PROTECTIVE PACKAGING SOLUTIONS</div>
  </section>

  <section class="card card-back" aria-label="Card back">
    <svg class="wave" viewBox="0 0 540 310" aria-hidden="true">
      <path d="M0 0 H190 C230 60 250 150 215 230 C200 265 210 295 225 310 H0 Z" fill="var(--brand-red)"/>
      <path d="M0 0 H180 C220 60 238 150 203 230 C188 265 198 295 212 310 H0 Z" fill="var(--card-black)"/>
      <rect x="58" y="110" width="90" height="90" fill="var(--brand-red)"/>
    </svg>
    <div class="contact">
      <div class="person-name">DARA OYELARAN</div>
      <div class="person-title">General Manager</div>
      <ul class="details">
        <li class="address">14 Larkin Road Brenmoor NSW 2764</li>
        <li><svg viewBox="0 0 12 12"><path d="M2 1 L4.5 1 L5.5 3.5 L4 4.5 C4.8 6.3 5.7 7.2 7.5 8 L8.5 6.5 L11 7.5 L11 10 C11 10.6 10.5 11 10 11 C5 11 1 7 1 2 C1 1.5 1.4 1 2 1 Z"/></svg>02 9471 5826</li>
        <li><svg viewBox="0 0 12 12"><rect x="3" y="1" width="6" height="3"/><rect x="1" y="4.5" width="10" height="4.5" rx="1"/><rect x="3" y="8" width="6" height="3"/></svg>9471 5839</li>
        <li><svg viewBox="0 0 12 12"><path d="M3.5 0.5 H8.5 A1 1 0 0 1 9.5 1.5 V10.5 A1 1 0 0 1 8.5 11.5 H3.5 A1 1 0 0 1 2.5 10.5 V1.5 A1 1 0 0 1 3.5 0.5 Z M4 2 V9 H8 V2 Z"/></svg>0438 217 564</li>
        <li><svg viewBox="0 0 12 12"><path d="M0.5 2.5 H11.5 V9.5 H0.5 Z M1.5 3.5 L6 7 L10.5 3.5 Z" fill-rule="evenodd"/></svg>dara.oyelaran@cushtane.com.au</li>
        <li><svg viewBox="0 0 12 12"><circle cx="6" cy="6" r="5.5"/><path d="M0.5 6 H11.5 M6 0.5 V11.5" stroke="#fff" stroke-width="0.8"/></svg>www.cushtane.com.au</li>
      </ul>
    </div>
  </section>
</main>
</body>
</html>
```